Home Page Design (+50 More Pages To Winning Designer!)

We have a 50+ page website, but we're starting with the home page. The winning designer will get all 50+ pages to design as a 2nd project, so make sure you do your best!

Velorane is in the private jet industry and needs a re-designed website.

We have created the structure for the website and content inside of Frandle.io (THESE ARE ONLY ROUGH A.I. GENERATED WIREFRAMES AND DO NOT NEED TO BE FOLLOWED EXACTLY) - https://www.frandle.io/app/project/K482915_qWmRtZaLs-KDnHoUvvy82QJ5cfhaR61trkwqlDV3Hm

Take the content from the 'Home Page' under the 'Wireframe' tab on the Frandle.io link above, but feel free to re-design the page in a better way as these are only A.I. generated wireframes.

We want a DARK theme.... High quality, luxurious feel, greyscale colors. Attached is a brand guideline (BUT THIS IS NOT A 100% BRAND GUIDELINE, YOU CAN CHANGE COLORS AND FONTS AND MAKE CHANGES IF YOU HAVE BETTER IDEAS) and attached is our logo. We are also attaching some examples of other apps and websites to give you a guideline of what we're looking for for this design project.

The final design MUST communicate luxury using high-quality imagery of large cabin luxurious private jets.
Updates

ENTRIES THAT DO NOT FOLLOW THE PROJECT BRIEF WILL BE AUTOMATICALLY DISCARDED. FOLLOW THE INSTRUCTIONS!

Industry/Entity Type

Travel

Number of Pages Required

1 page

Font styles to use
Sans Serif

Colors

Designer to choose colors to be used in the design.

Requirements
Must have
• Follow wireframe and use content in wireframe (see Frandle.io link)

```html
<!DOCTYPE html>
<html lang="en">
<head>
<meta charset="utf-8">
<title>Velorane — Luxury Jet Travel</title>
<link rel="stylesheet" href="https://fonts.googleapis.com/css2?family=Roboto:wght@400;500;700&family=DM+Sans:wght@500;600&display=swap">
<style>
:root{
  --bg:#000;
  --outer:#fff;
  --text:#fff;
  --muted:#cfcfcf;
  --line:#8a8a8a;
  --sky:linear-gradient(160deg,#b9cbe0,#e6edf5 55%,#9fb6d1);
  --sunset:linear-gradient(175deg,#3b3426,#b08a4a 40%,#6b4a2a 70%,#1e1a16);
  --dusk:linear-gradient(180deg,#5a5e62,#9a9c9c 45%,#3a3630 75%,#1b1a18);
  --cabin:linear-gradient(160deg,#8f877c,#e9e2d6 50%,#b8ad9e);
  --pilot:linear-gradient(160deg,#2c2a28,#6c5f55 45%,#20252e);
  --tarmac:linear-gradient(180deg,#c9d4de,#eef1f4 40%,#8d8d8a 60%,#4b4a48);
}
*{margin:0;padding:0;box-sizing:border-box}
html,body{width:1200px;height:3542px;overflow:hidden;background:var(--outer)}
body{font-family:Roboto,Arial,sans-serif;color:var(--text);-webkit-font-smoothing:antialiased;-moz-osx-font-smoothing:grayscale;text-rendering:geometricPrecision}
.page{position:relative;width:1155px;height:3542px;background:var(--bg);overflow:hidden}
.abs{position:absolute}
.photo{position:absolute}
h1,h2{font-weight:500;line-height:1.1;letter-spacing:.2px;color:var(--text)}
.h-xl{font-size:44px;white-space:nowrap}
.p{font-size:16px;line-height:22.5px;color:var(--text)}
.btn{position:absolute;display:flex;align-items:center;justify-content:center;gap:10px;font-size:15px;font-weight:500;border:1.5px solid #fff;height:38px}
.btn.solid{background:#fff;color:#000}
.btn.ghost{color:#fff}
.nav a{position:absolute;top:26px;font-size:11px;color:#fff;text-decoration:none}
.logo-sm{position:absolute;left:82px;top:24px;font-size:14px;display:flex;align-items:center;gap:4px}
.logo-sm i{display:block;width:8px;height:8px;background:#fff}
.nav .btn{height:33px;font-size:11px;font-weight:700}
.list{position:absolute;left:72px}
.list div{position:absolute;left:0;display:flex;align-items:center;gap:16px;font-size:16px;white-space:nowrap;color:var(--text)}
.feat h3{position:absolute;left:543px;font-size:30px;font-weight:400;white-space:nowrap}
.feat p{position:absolute;left:543px;width:540px;font-size:15.5px;line-height:22.5px;color:var(--text)}
.mini h4{font-size:16px;font-weight:700;margin-bottom:10px}
.mini p{font-size:9.5px;line-height:23px;width:180px;color:var(--text)}
.trusted{position:absolute;left:0;width:1155px;top:2530px;text-align:center;font-family:"DM Sans",sans-serif;font-weight:600;font-size:36px}
.card{position:absolute;top:2605px;width:413px;height:280px;border:1.5px solid #fff;padding:40px 38px}
.stars{font-size:25px;letter-spacing:5px;line-height:1}
.card p{margin-top:14px;font-size:14px;line-height:23px;color:var(--muted);white-space:nowrap}
.who{margin-top:18px;display:flex;align-items:center;gap:14px}
.avatar{width:57px;height:57px;border-radius:50%;background:linear-gradient(160deg,#e6b84c,#8a6a3a)}
.who b{display:block;font-size:16px;font-weight:700}
.who span{font-size:10px;color:var(--muted);white-space:nowrap}
.foot-col{position:absolute;top:3194px}
.foot-col h5{font-size:16px;font-weight:700;letter-spacing:.3px;margin-bottom:16px}
.foot-col a{display:block;font-size:14.5px;color:#e5e5e5;text-decoration:none}
.contact{position:absolute;left:72px;display:flex;align-items:center;gap:14px;font-size:14.5px}
.rule{position:absolute;left:0;width:1155px;height:1px;background:#555}
</style>
</head>
<body>
<div class="page">

<nav class="nav">
  <div class="logo-sm">Velorane<i></i></div>
  <a style="left:330px" href="#">Aircraft</a>
  <a style="left:405px" href="#">Programs</a>
  <a style="left:487px" href="#">Why Velorane</a>
  <a style="left:585px" href="#">Lifestyle</a>
  <div class="btn ghost" style="left:799px;top:16px;width:146px">Featured From Blog</div>
  <div class="btn solid" style="left:972px;top:16px;width:105px">Article Title</div>
</nav>

<section class="hero">
  <h1 class="abs h-xl" style="left:72px;top:225px">Experience The<br>Ultimate In<br>Luxury Jet Travel</h1>
  <p class="abs p" style="left:72px;top:401px;width:335px">Velorane offers fractional jet ownership, jet card programs, private jet lease programs, all access programs, helicopter access programs, and by the seat charter flights. Discover the perfect flight program for your needs.</p>
  <div class="btn solid" style="left:72px;top:538px;width:93px">Explore</div>
  <div class="btn ghost" style="left:190px;top:538px;width:118px">Learn More</div>
  <div class="photo" role="img" aria-label="Jet wing above the clouds" style="left:420px;top:65px;width:319px;height:148px;background:var(--sky)"></div>
  <div class="photo" role="img" aria-label="Private jet on a runway at sunset" style="left:420px;top:240px;width:319px;height:319px;background:var(--sunset)"></div>
  <div class="photo" role="img" aria-label="Airliner flying through a blue sky" style="left:420px;top:586px;width:319px;height:145px;background:var(--sky)"></div>
  <div class="photo" role="img" aria-label="Large jet parked at golden hour" style="left:758px;top:65px;width:319px;height:320px;background:var(--sunset)"></div>
  <div class="photo" role="img" aria-label="Private jet facing forward on the runway" style="left:758px;top:412px;width:319px;height:319px;background:var(--dusk)"></div>
</section>

<section>
  <h2 class="abs h-xl" style="left:72px;top:838px">Experience The Luxury Of<br>Fractional Jet Ownership</h2>
  <p class="abs p" style="left:72px;top:962px;width:545px">With velorane's fractional jet ownership programs, you can enjoy the benefits of private jet travel without the hassle and expense of owning a whole aircraft. Our program offers flexibility, convenience, and access to a fleet of luxurious jets, allowing you to travel in style and comfort.</p>
  <div class="list">
    <div style="top:1077px"><svg width="16" height="16" viewBox="0 0 16 16"><path d="M3 13L13 3M5 3h8v8" stroke="#fff" stroke-width="1.4" fill="none"/></svg>Flexible Ownership Options</div>
    <div style="top:1127px"><svg width="16" height="16" viewBox="0 0 16 16"><path d="M3 13L13 3M5 3h8v8" stroke="#fff" stroke-width="1.4" fill="none"/></svg>Convenient Booking Process</div>
    <div style="top:1177px"><svg width="16" height="16" viewBox="0 0 16 16"><path d="M3 13L13 3M5 3h8v8" stroke="#fff" stroke-width="1.4" fill="none"/></svg>Luxurious Fleet Of Jets</div>
  </div>
  <div class="btn solid" style="left:72px;top:1225px;width:119px">Learn More</div>
  <div class="btn ghost" style="left:215px;top:1223px;width:125px;height:42px">Sign Up <svg width="14" height="14" viewBox="0 0 16 16"><path d="M3 13L13 3M5 3h8v8" stroke="#fff" stroke-width="1.5" fill="none"/></svg></div>
  <div class="photo" role="img" aria-label="Pilot seated in a jet cockpit" style="left:649px;top:786px;width:434px;height:527px;background:var(--pilot)"></div>
</section>

<section class="feat">
  <div class="photo" role="img" aria-label="Private jet parked with its airstair open" style="left:72px;top:1366px;width:433px;height:528px;background:var(--tarmac)"></div>
  <div class="abs" style="left:529px;top:1446px;width:1px;height:104px;background:#fff"></div>
  <h3 style="top:1446px">Flexible Ownership Options Available</h3>
  <p style="top:1506px">Choose from a variety of ownership programs and enjoy the freedom to fly on your own terms.</p>
  <h3 style="top:1578px">Convenient Jet Card Programs</h3>
  <p style="top:1638px">Access a fleet of private jets with our exclusive jet card programs, offering flexibility and convenience.</p>
  <h3 style="top:1710px">Flexible Lease Programs</h3>
  <p style="top:1770px">Experience the luxury of private jet travel without the commitment with our flexible lease programs.</p>
</section>

<section>
  <h2 class="abs h-xl" style="left:72px;top:2005px">Unparalleled Luxury And<br>Convenience For Private<br>Aviation</h2>
  <p class="abs p" style="left:72px;top:2181px;width:545px">Discover the ultimate in luxury and convenience with velorane. Our exclusive private aviation solutions provide you with unparalleled access to the world of private jets, ensuring a seamless and extraordinary travel experience.</p>
  <div class="abs mini" style="left:72px;top:2278px"><h4>Convenience</h4><p>Enjoy hassle-free travel with our flexible scheduling and personalized services.</p></div>
  <div class="abs mini" style="left:406px;top:2278px"><h4>Luxury</h4><p>Indulge in the lavish amenities and exquisite interiors of our private jets</p></div>
  <div class="btn solid" style="left:72px;top:2376px;width:119px">Learn More</div>
  <div class="btn ghost" style="left:215px;top:2374px;width:125px;height:42px">Sign Up <svg width="14" height="14" viewBox="0 0 16 16"><path d="M3 13L13 3M5 3h8v8" stroke="#fff" stroke-width="1.5" fill="none"/></svg></div>
  <div class="photo" role="img" aria-label="Cream leather seats in a private jet cabin" style="left:649px;top:1949px;width:434px;height:526px;background:var(--cabin)"></div>
</section>

<section>
  <h2 class="trusted">Trusted by 25k+ Customers!</h2>
  <div class="card" style="left:72px">
    <div class="stars">★★★★★</div>
    <p>Minim veniam, quis nostrud exercitation ullamco<br>laboris nisi ut aliquip ex ea commodo consequat.<br>Duis aute irure dolor in reprehenderit in voluptate<br>velit esse cillum dolore eu fugiat nulla pariatur.</p>
    <div class="who"><div class="avatar" role="img" aria-label="Customer portrait"></div><div><b>Mira Kelen</b><span>Dog Trainer</span></div></div>
  </div>
  <div class="card" style="left:512px">
    <div class="stars">★★★★★</div>
    <p>Minim veniam, quis nostrud exercitation ullamco<br>laboris nisi ut aliquip ex ea commodo consequat.<br>Duis aute irure dolor in reprehenderit in voluptate<br>velit esse cillum dolore eu fugiat nulla pariatur.</p>
    <div class="who"><div class="avatar" role="img" aria-label="Customer portrait"></div><div><b>Arlo</b><span>President of Sales</span></div></div>
  </div>
  <div class="card" style="left:952px;overflow:hidden">
    <div class="stars">★★★★★</div>
    <p>Minim veniam, quis nostrud exercitation ullamco<br>laboris nisi ut aliquip ex ea commodo consequat.<br>Duis aute irure dolor in reprehenderit in voluptate<br>velit esse cillum dolore eu fugiat nulla pariatur.</p>
    <div class="who"><div class="avatar" role="img" aria-label="Customer portrait" style="background:linear-gradient(160deg,#b58ad0,#5a3a6a)"></div><div><b>Tessa Vorin</b><span>Marketing Coordinator</span></div></div>
  </div>
</section>

<section>
  <h2 class="abs" style="left:72px;top:2940px;font-size:38px;white-space:nowrap">Experience Luxury Travel<br>Like Never Before</h2>
  <p class="abs p" style="left:540px;top:2937px;width:545px">Discover the ultimate in private jet travel with velorane. Whether you're looking for fractional jet ownership, jet card programs, private jet lease programs, all access programs, helicopter access programs, or by the seat charter flights, we have the perfect solution for you travel needs.</p>
  <div class="btn solid" style="left:540px;top:3054px;width:77px">Book</div>
  <div class="btn ghost" style="left:642px;top:3054px;width:96px">Contact</div>
</section>

<footer>
  <div class="rule" style="top:3145px"></div>
  <div class="abs" style="left:70px;top:3236px;font-size:56px;font-weight:400;letter-spacing:1px;line-height:1">Velorane</div>
  <div class="contact" style="top:3311px"><svg width="18" height="18" viewBox="0 0 18 18"><path d="M9 16s5-5 5-9a5 5 0 0 0-10 0c0 4 5 9 5 9z" stroke="#fff" stroke-width="1.4" fill="none"/><circle cx="9" cy="7" r="1.8" stroke="#fff" stroke-width="1.4" fill="none"/></svg>2208 Harbor Lane, Fairmont Bay 40917</div>
  <div class="contact" style="top:3348px"><svg width="18" height="18" viewBox="0 0 18 18"><path d="M4 2h3l1.5 4-2 1.2a9 9 0 0 0 4.3 4.3L12 9.5l4 1.5v3a2 2 0 0 1-2 2A12 12 0 0 1 2 4a2 2 0 0 1 2-2z" stroke="#fff" stroke-width="1.4" fill="none"/></svg>555.018.4420</div>
  <div class="contact" style="top:3385px"><svg width="18" height="18" viewBox="0 0 18 18"><rect x="2" y="4" width="14" height="10" stroke="#fff" stroke-width="1.4" fill="none"/><path d="M2 4l7 6 7-6" stroke="#fff" stroke-width="1.4" fill="none"/></svg>Halo@Velorane.com</div>
  <div class="foot-col" style="left:487px"><h5>ABOUT US</h5><a style="margin-bottom:13px">Charter</a><a style="margin-bottom:13px">Fleet</a><a style="margin-bottom:13px">Destinations</a><a>Pricing</a></div>
  <div class="foot-col" style="left:762px"><h5>SERVICES</h5><a style="margin-bottom:24px">Private Jets</a><a style="margin-bottom:24px">Helicopters</a><a>Jet Cards</a></div>
  <div class="foot-col" style="left:942px"><h5>TERMS</h5><a style="margin-bottom:24px">Privacy</a><a>Careers</a></div>
  <div class="rule" style="top:3475px;background:#777"></div>
  <div class="abs" style="left:0;width:1155px;top:3487px;text-align:center;font-size:10px">Copyright © 2023 Velorane</div>
</footer>

</div>
</body>
</html>
```